KTWG application splash screen

We need a 1024x768 image for use as an application splash screen.
The image will be displayed full screen on an 10 inch industrial PC 1024x768 screen while our application is launching. The image should convey that the application is "Waiting for connection to Wi-Fi access point..." and include a graphic of the industrial PC connected to the access point via an Ethernet cable. A list of troubleshooting steps should be included at the bottom of the image. The troubleshooting steps should not be the main focus of the image and should be shown in a smaller font (but still readable at 1024x768 displayed on a 10 inch screen).
I will include a mock up of the general idea of what we are looking for as well as image files for the industrial PC, a screenshot of our application to show on the PC's screen and the AP.
For general look and feel and a sense of corporate branding please review our website https://marrowgatesoilworks.example/. The splash screen should reflect corporate branding.
Target Market(s)
Users of our application
Industry/Entity Type
Agriculture
Look and feel

```html
<!DOCTYPE html>
<html lang="en">
<head>
<meta charset="utf-8">
<title>KTWG splash screen – waiting for Wi-Fi</title>
<link href="https://fonts.googleapis.com/css2?family=Poppins:wght@400;500;600;700&display=swap" rel="stylesheet">
<style>
  :root{
    --backdrop:#000000;
    --deep:#1c2a22;
    --dark-green:#26412f;
    --mid-green:#2f7d47;
    --bright-green:#4fd37a;
    --brand-green:#3cb964;
    --white:#ffffff;
    --soft-white:#e9f6ee;
  }
  *{box-sizing:border-box;margin:0;padding:0}
  html,body{width:1200px;height:1200px;overflow:hidden;background:var(--backdrop)}
  body{font-family:"Poppins",sans-serif;position:relative}
  .splash{position:absolute;left:110px;top:233px;width:978px;height:733px;overflow:hidden;background:var(--deep)}
  .splash-bg{position:absolute;inset:0;width:100%;height:100%}
  .title-card{position:absolute;left:283px;top:0;width:413px;height:163px;background:var(--white);border-radius:0 0 16px 16px;display:flex;align-items:center;justify-content:center;padding-top:24px}
  .title-card h1{color:var(--brand-green);font-weight:600;font-size:31.5px;line-height:34.5px;text-align:center;letter-spacing:1.3px}
  .device{position:absolute;width:262px;height:262px;border-radius:50%;background:var(--white);text-align:center}
  .device--computer{left:51px;top:238px}
  .device--ap{left:665px;top:238px}
  .device-photo{position:absolute}
  .device--computer .device-photo{left:42px;top:24px;width:178px;height:143px;border-radius:8px;background:linear-gradient(160deg,#2b2b2b,#121212)}
  .device--computer .device-photo::after{content:"";position:absolute;left:17px;top:13px;width:144px;height:108px;background:linear-gradient(180deg,#f4f6f5,#d9eee0)}
  .device--ap .device-photo{left:118px;top:23px;width:26px;height:148px;border-radius:6px;background:linear-gradient(90deg,#d8dcdb,#ffffff,#d8dcdb)}
  .device-name{position:absolute;left:0;right:0;top:180px;color:var(--brand-green);font-weight:600;font-size:17.5px;letter-spacing:1px}
  .device-sub{position:absolute;left:0;right:0;top:202px;color:var(--brand-green);font-weight:400;font-size:13.5px;letter-spacing:.6px}
  .link{position:absolute;left:335px;top:366px;width:310px;height:8px}
  .link-label{position:absolute;left:283px;top:383px;width:413px;text-align:center;color:var(--white);font-weight:600;font-size:18.5px;letter-spacing:1.4px}
  .troubleshoot{position:absolute;left:276px;top:579px;width:426px;height:154px;background:var(--white);border-radius:14px 14px 0 0;color:var(--brand-green);padding:11px 32px 0 28px}
  .troubleshoot h2{font-weight:600;font-size:13.5px;letter-spacing:1px;text-align:center;margin-left:-28px;margin-right:-32px;margin-bottom:3px}
  .troubleshoot ul{list-style:none;font-size:9.6px;line-height:11.5px}
  .troubleshoot li::before{content:"• "}
  .troubleshoot ul ul{padding-left:12px}
  .troubleshoot ul ul li{padding-left:7px;text-indent:-7px}
  .brand-tag{position:absolute;left:858px;top:615px;width:88px;height:84px;display:flex;align-items:center;justify-content:center;gap:6px}
  .brand-square{width:12px;height:12px;background:var(--white)}
  .brand-name{color:var(--white);font-weight:700;font-size:22px;letter-spacing:.5px}
</style>
</head>
<body>
<main class="splash">
  <svg class="splash-bg" viewBox="0 0 978 733" preserveAspectRatio="none" aria-hidden="true">
    <defs>
      <linearGradient id="base" x1="0" y1="0" x2="1" y2="1">
        <stop offset="0" stop-color="#2a5a3a"/><stop offset=".5" stop-color="#1f2c24"/><stop offset="1" stop-color="#1a231e"/>
      </linearGradient>
      <radialGradient id="glowTR" cx="1" cy="0" r="1">
        <stop offset="0" stop-color="#7ee8a0"/><stop offset=".45" stop-color="#34a85a"/><stop offset="1" stop-color="#1f2c24" stop-opacity="0"/>
      </radialGradient>
      <radialGradient id="glowBL" cx="0" cy="1" r="1">
        <stop offset="0" stop-color="#7ee8a0"/><stop offset=".45" stop-color="#33a358"/><stop offset="1" stop-color="#1f2c24" stop-opacity="0"/>
      </radialGradient>
      <linearGradient id="panelTL" x1="0" y1="0" x2="1" y2="1">
        <stop offset="0" stop-color="#3aa85c"/><stop offset="1" stop-color="#2b7443"/>
      </linearGradient>
    </defs>
    <rect width="978" height="733" fill="url(#base)"/>
    <rect width="978" height="733" fill="url(#glowTR)" opacity=".9"/>
    <rect width="978" height="733" fill="url(#glowBL)" opacity=".9"/>
    <polygon points="0,0 283,0 283,60 196,60 130,135 0,135" fill="url(#panelTL)"/>
    <polygon points="40,130 230,130 260,146 32,146" fill="#3a9e58"/>
    <polygon points="745,608 978,608 978,733 720,733 790,660" fill="#2f8a4c"/>
    <path d="M0 520 C160 530 300 560 420 733 L0 733 Z" fill="#48c06e" opacity=".55"/>
    <path d="M700 160 C800 230 900 250 978 245 L978 0 L700 0 Z" fill="#52cf7c" opacity=".4"/>
  </svg>

  <header class="title-card">
    <h1>Waiting for<br>connection to Wi-Fi<br>access point...</h1>
  </header>

  <section class="device device--computer">
    <div class="device-photo" role="img" aria-label="Photo of the rugged tractor cab computer showing the seeding application"></div>
    <p class="device-name">TRACTOR CAB</p>
    <p class="device-sub">COMPUTER</p>
  </section>

  <svg class="link" viewBox="0 0 310 8" aria-hidden="true">
    <g fill="#ffffff">
      <circle cx="4" cy="4" r="2.3"/><circle cx="14.5" cy="4" r="2.3"/><circle cx="25" cy="4" r="2.3"/><circle cx="35.5" cy="4" r="2.3"/><circle cx="46" cy="4" r="2.3"/><circle cx="56.5" cy="4" r="2.3"/><circle cx="67" cy="4" r="2.3"/><circle cx="77.5" cy="4" r="2.3"/><circle cx="88" cy="4" r="2.3"/><circle cx="98.5" cy="4" r="2.3"/><circle cx="109" cy="4" r="2.3"/><circle cx="119.5" cy="4" r="2.3"/><circle cx="130" cy="4" r="2.3"/><circle cx="140.5" cy="4" r="2.3"/><circle cx="151" cy="4" r="2.3"/><circle cx="161.5" cy="4" r="2.3"/><circle cx="172" cy="4" r="2.3"/><circle cx="182.5" cy="4" r="2.3"/><circle cx="193" cy="4" r="2.3"/><circle cx="203.5" cy="4" r="2.3"/><circle cx="214" cy="4" r="2.3"/><circle cx="224.5" cy="4" r="2.3"/><circle cx="235" cy="4" r="2.3"/><circle cx="245.5" cy="4" r="2.3"/><circle cx="256" cy="4" r="2.3"/><circle cx="266.5" cy="4" r="2.3"/><circle cx="277" cy="4" r="2.3"/><circle cx="287.5" cy="4" r="2.3"/><circle cx="298" cy="4" r="2.3"/><circle cx="306" cy="4" r="2.3"/>
    </g>
  </svg>
  <p class="link-label">ETHERNET CABLE</p>

  <section class="device device--ap">
    <div class="device-photo" role="img" aria-label="Photo of the white outdoor Wi-Fi access point with two antennas"></div>
    <p class="device-name">WI-FI ACCESS POINT</p>
    <p class="device-sub">TR-NODE AX40-OUTDOOR</p>
  </section>

  <section class="troubleshoot">
    <h2>TROUBLESHOOTING STEPS:</h2>
    <ul>
      <li>This screen should only be visible for a short time on boot.</li>
      <li>If this screen stays visible for more than a minute:
        <ul>
          <li>Verify that the Wi-Fi Access Point (AP) powers up when this system does (indicated by a green light on the side of the AP).</li>
          <li>Check the Ethernet cable between this system and the AP for damage, and replace it if necessary.</li>
          <li>Power-cycle this system and wait for it to reboot fully.</li>
          <li>If the issue persists, contact KTWG support for further assistance.</li>
        </ul>
      </li>
    </ul>
  </section>

  <div class="brand-tag">
    <span class="brand-square"></span>
    <span class="brand-name">KTWG</span>
  </div>
</main>
</body>
</html>
```